School Website

I need a design for a School (2 sections: Primary 6-12 years and Secondary 12-18 years). The first page is just a choice of the 2 sections. After we'll need 2 websites (with the same structure: Menu, ...) but with different colors. In fact, we need for end of October, 6 design of school website. So the best websites are going to be made available to you in the future (in pixelharbor) but privately.

Target Market(s)

Public, Parents, ...

Coding

Coded - Design and coding required

Number of Pages Required

5+ page

Font styles to use
Sans Serif

Colors
34a6d7
85cae6
cee9f5
ffffff

Requirements
Must have
• You can check the old Website: http: / /velmot.be We need the same pages with the same content. Menu: - HomePage - News and communication (like blog page) - Activities (like blog page, with photo gallery) - Contact (Contact form + maps) - In the main menu, we need a special button to connect to an external Website ( button needs to be different than the other menu items The name of this button is "Parents Area"). The logo of 2 sections are attached. Please use it for the design and the choice of colors.
Nice to have
• This is a web design of other school that we like: https://www.quintelo.be

```html
<!DOCTYPE html>
<html lang="en">
<head>
<meta charset="utf-8">
<title>Athénée Royal de Velmot – Kindergarten and Primary</title>
<link rel="stylesheet" href="https://fonts.googleapis.com/css2?family=Source+Sans+3:ital,wght@0,400;0,600;0,700;1,400&display=swap">
<style>
:root{
  --blue:#34a6d7;
  --blue-mid:#85cae6;
  --blue-light:#cee9f5;
  --white:#ffffff;
  --ink:#333333;
  --muted:#777777;
  --soft:#f3f3f3;
  --dark:#3e3e3e;
  --darker:#2f2f2f;
  --line:#e4e4e4;
}
*{box-sizing:border-box;margin:0;padding:0}
html,body{width:1200px;height:4392px;overflow:hidden;background:var(--white)}
body{font-family:"Source Sans 3",Arial,sans-serif;color:var(--ink)}
.page{position:relative;width:1200px;height:4392px;overflow:hidden}
.abs{position:absolute}
svg{display:block}

/* top bar */
.topbar{left:0;top:0;width:1200px;height:41px;background:var(--blue);color:var(--white);font-size:15px;font-weight:600}
.topbar .item{position:absolute;top:11px;display:flex;align-items:center;gap:7px}
.topbar .social{position:absolute;right:48px;top:10px;display:flex;gap:8px}
.topbar .social span{width:21px;height:21px;border:2px solid var(--white);border-radius:50%}

/* header */
.header{left:0;top:41px;width:1200px;height:92px;background:var(--white)}
.brand{position:absolute;left:50px;top:24px;display:flex;align-items:center;gap:10px}
.brand .dot{width:44px;height:44px;border-radius:50%;background:var(--blue)}
.brand .name{font-size:24px;font-weight:700;color:var(--blue)}
.nav{position:absolute;top:36px;left:490px;display:flex;gap:36px;font-size:15px;font-weight:700;color:var(--ink)}
.parents-btn{position:absolute;left:1007px;top:27px;width:144px;height:38px;border-radius:19px;background:var(--blue);color:var(--white);font-size:16px;font-weight:700;display:flex;align-items:center;justify-content:center;box-shadow:0 3px 0 var(--blue-mid)}

/* hero */
.hero{left:0;top:133px;width:1200px;height:460px;
  background:
    linear-gradient(180deg,rgba(255,255,255,0) 70%,rgba(120,110,100,.35) 100%),
    linear-gradient(90deg,#d9c7d8 0%,#9aa9d6 10%,#7a5aa6 20%,#8a5fa8 30%,#6fb9d6 42%,#a9e3ea 50%,#6fb3d4 58%,#3f6fb0 66%,#c9a079 74%,#2f5fa8 80%,#d95a5a 86%,#e8c5a6 92%,#3b3f4c 100%)}
.hero-text{position:absolute;left:0;top:238px;width:1200px;text-align:center;color:var(--white);text-shadow:0 2px 6px rgba(0,0,0,.45)}
.hero-text h1{font-size:52px;font-weight:400;line-height:64px}
.hero-text .sub{font-size:25px;font-weight:600;margin-top:-6px}
.call-btn{position:absolute;left:505px;top:435px;width:191px;height:51px;border-radius:26px;background:var(--blue);color:var(--white);font-size:20px;font-weight:600;display:flex;align-items:center;justify-content:center;gap:12px}

/* info cards */
.info-card{top:687px;width:350px;height:125px;background:var(--white);border-radius:14px;box-shadow:0 0 8px rgba(0,0,0,.18);display:flex;align-items:center}
.info-card .ico{width:75px;height:75px;border-radius:50%;background:var(--blue);margin-left:30px;display:flex;align-items:center;justify-content:center;flex-shrink:0}
.info-card .txt{font-size:16px;font-weight:700;line-height:22px;color:var(--ink);margin-left:38px}
.info-card .txt.center{text-align:center}

.section-title{font-size:30px;font-weight:700;color:var(--ink);letter-spacing:.5px}

/* schedules */
.sched-card{top:941px;width:537px;height:430px;background:var(--white);box-shadow:0 0 8px rgba(0,0,0,.16)}
.sched-card .head{height:183px;border-bottom:1px solid var(--line);text-align:center}
.sched-card .head .ico{margin:28px auto 0;width:94px;height:94px}
.sched-card .head h3{font-size:19px;font-weight:700;color:var(--blue);margin-top:16px}
.sched-list{list-style:none;position:relative}
.sched-list li{position:absolute;left:22px;display:flex;align-items:flex-start;gap:22px;font-size:14px;color:#555;text-transform:uppercase;line-height:20px}
.sched-list li svg{flex-shrink:0;margin-top:-4px}
.note{left:0;top:1396px;width:1200px;text-align:center;font-size:14px;font-weight:700;color:var(--blue);line-height:22px}

/* news */
.news-bg{left:0;top:1487px;width:1200px;height:602px;background:var(--soft)}
.slider-arrows{display:flex;gap:16px}
.slider-arrows span{width:27px;height:20px;background:var(--blue);display:flex;align-items:center;justify-content:center}
.news-card{top:1616px;width:348px;height:413px;background:var(--white);box-shadow:0 0 6px rgba(0,0,0,.14)}
.news-card .photo{height:173px}
.news-card .badge{position:absolute;left:0;top:4px;width:68px;height:48px;background:var(--blue);color:var(--white);font-size:16px;font-weight:700;line-height:18px;text-align:center;padding-top:5px}
.news-card h4{position:absolute;left:26px;top:193px;font-size:20px;font-weight:600;color:var(--ink)}
.news-card .meta{position:absolute;left:26px;top:248px;width:300px;display:flex;font-size:14px;color:var(--muted)}
.news-card .meta span{display:flex;align-items:center;gap:12px}
.news-card .meta span:last-child{margin-left:auto}
.news-card p{position:absolute;left:26px;top:288px;width:300px;font-size:13px;color:var(--muted);line-height:23px}
.news-card .more{position:absolute;left:26px;top:373px;font-size:14px;font-weight:700;color:var(--blue)}

/* team */
.team-box{left:51px;top:2140px;width:738px;height:503px;background:var(--white);box-shadow:0 0 8px rgba(0,0,0,.16)}
.member{position:absolute;top:126px;width:240px;text-align:center}
.member .avatar{width:156px;height:156px;margin:0 auto;border-radius:50%;border:7px solid var(--blue);border-left-color:#d9d9d9;border-top-color:#d9d9d9}
.member h4{font-size:20px;font-weight:700;color:var(--blue);margin-top:20px;text-transform:uppercase}
.member .section{font-size:14px;font-style:italic;color:var(--muted);margin-top:4px}
.member .class{font-size:14px;font-weight:600;color:#555;margin-top:6px}
.dots{position:absolute;left:311px;top:432px;display:flex;gap:20px;align-items:center}
.dots span{width:13px;height:13px;border-radius:50%;background:var(--blue)}
.dots span.on{width:19px;height:19px;border:3px solid var(--blue);background:var(--white);box-shadow:inset 0 0 0 3px var(--white),inset 0 0 0 8px var(--blue)}

.contacts-box{left:820px;top:2140px;width:333px;height:503px;background:var(--white);box-shadow:0 0 8px rgba(0,0,0,.16)}
.contacts-inner{position:absolute;left:36px;top:107px;width:261px;height:362px;background:var(--white);box-shadow:0 0 6px rgba(0,0,0,.14)}
.contact-entry{position:absolute;left:26px;width:212px;padding-bottom:16px;border-bottom:1px solid #ccc}
.contact-entry h5{font-size:16px;font-weight:700;color:var(--blue)}
.contact-entry .role{font-size:14px;font-style:italic;color:var(--muted);margin-top:6px}
.contact-entry .tel{font-size:14px;color:var(--muted);margin-top:12px;display:flex;align-items:center;gap:12px}
.view-all{position:absolute;left:51px;top:281px;width:159px;height:47px;border-radius:24px;background:var(--blue);color:var(--white);font-size:15px;font-weight:600;display:flex;align-items:center;justify-content:center;gap:8px;box-shadow:0 3px 0 var(--blue-mid)}

/* activities */
.activity-card{left:51px;top:2837px;width:585px;height:189px;background:var(--white);box-shadow:0 0 6px rgba(0,0,0,.14)}
.activity-card .photo{position:absolute;left:0;top:0;width:234px;height:189px;
  background:linear-gradient(180deg,#e9e4dc 0%,#c98f5c 18%,#f1ece4 38%,#d7cfc4 60%,#8e6a4c 80%,#b0a69a 100%)}
.activity-card .date{position:absolute;left:0;top:0;width:60px;height:108px;background:var(--blue);color:var(--white);font-weight:700;text-align:center;padding-top:22px;font-size:20px;line-height:30px}
.activity-card h4{position:absolute;left:261px;top:34px;font-size:20px;font-weight:600}
.activity-card .row{position:absolute;left:261px;display:flex;align-items:center;gap:18px;font-size:14px;color:#555}
.v-sep{left:662px;top:2750px;width:1px;height:290px;background:#ddd}
.rules-box{left:694px;top:2757px;width:459px;height:283px;background:var(--white);box-shadow:0 0 6px rgba(0,0,0,.14);overflow:hidden}
.rules-box .deco{position:absolute;border-radius:50%;background:var(--blue-light);opacity:.7}
.rules-box h3{position:absolute;left:0;top:26px;width:459px;text-align:center;font-size:30px;font-weight:700;color:var(--ink)}
.rules-box p{position:absolute;left:0;top:80px;width:459px;text-align:center;font-size:20px;color:var(--muted);line-height:28px}
.rules-btn{position:absolute;left:126px;top:167px;width:208px;height:68px;border-radius:34px;background:var(--blue);color:var(--white);font-size:15px;font-weight:700;line-height:17px;display:flex;align-items:center;justify-content:center;gap:14px;box-shadow:0 3px 0 var(--blue-mid)}

/* gallery */
.gallery-bg{left:0;top:3095px;width:1200px;height:537px;background:var(--soft)}
.g-img{border:4px solid var(--white);box-shadow:0 0 5px rgba(0,0,0,.15)}

/* map + contact */
.map{left:51px;top:3686px;width:556px;height:420px;
  background:
    radial-gradient(circle at 38% 38%,rgba(230,90,80,.35) 0,rgba(230,90,80,0) 60px),
    linear-gradient(160deg,#cfe3ef 0%,#f2ecc4 18%,#f7f1d6 40%,#e6efc9 60%,#f4eccb 78%,#dbe8c6 100%)}
.contact-panel{left:607px;top:3686px;width:544px;height:420px;
  background:linear-gradient(180deg,#2d5a9a 0%,#213f6e 25%,#1c2c45 55%,#2a3340 80%,#1e2530 100%)}
.contact-panel h3{position:absolute;left:0;top:50px;width:544px;text-align:center;font-size:30px;font-weight:700;color:var(--white)}
.field{position:absolute;background:var(--white);border-radius:8px;font-size:14px;font-style:italic;color:#999;padding:13px 20px}
.submit{position:absolute;left:194px;top:321px;width:156px;height:54px;border-radius:27px;background:var(--blue);color:var(--white);font-size:20px;font-weight:700;display:flex;align-items:center;justify-content:center;gap:8px}

/* footer */
.footer-deco{left:0;top:4110px;width:1200px;height:140px}
.footer{left:0;top:4237px;width:1200px;height:155px;background:var(--dark)}
.footer .social{position:absolute;left:493px;top:44px;display:flex;gap:14px}
.footer .social span{width:42px;height:42px;border:3px solid var(--white);border-radius:50%}
.copyright{position:absolute;left:0;top:120px;width:1200px;height:35px;background:var(--darker);color:#cfcfcf;font-size:14px;text-align:center;line-height:35px}
</style>
</head>
<body>
<div class="page">

  <div class="abs topbar">
    <div class="item" style="left:50px">
      <svg width="16" height="16" viewBox="0 0 24 24"><path fill="#fff" d="M6.6 10.8a15.1 15.1 0 006.6 6.6l2.2-2.2c.3-.3.7-.4 1-.2 1.1.4 2.3.6 3.6.6.6 0 1 .4 1 1V20c0 .6-.4 1-1 1A17 17 0 013 4c0-.6.4-1 1-1h3.5c.6 0 1 .4 1 1 0 1.3.2 2.5.6 3.6.1.3 0 .7-.2 1z"/></svg>
      +32 81 40 17 55
    </div>
    <div class="item" style="left:202px">
      <svg width="17" height="16" viewBox="0 0 24 24"><path fill="#fff" d="M2 11l20-9-7 20-3-8z"/></svg>
      info@velmot-school.be
    </div>
    <div class="social"><span></span><span></span><span></span></div>
  </div>

  <header class="abs header">
    <div class="brand"><span class="dot"></span><span class="name">Athénée Royal de Velmot</span></div>
    <nav class="nav"><span>Home</span><span>News</span><span>Activities</span><span>Gallery</span><span>Contact</span></nav>
    <div class="parents-btn">Parents Area</div>
  </header>

  <section class="abs hero" role="img" aria-label="Photo of smiling schoolchildren with backpacks in a school corridor, a girl drawing on the left"></section>
  <div class="hero-text">
    <h1>WELCOME TO<br>Athenee Royal de Velmot</h1>
    <div class="sub">Kindergarten and Primary</div>
  </div>
  <div class="call-btn">
    <svg width="22" height="22" viewBox="0 0 24 24"><path fill="#fff" d="M6.6 10.8a15.1 15.1 0 006.6 6.6l2.2-2.2c.3-.3.7-.4 1-.2 1.1.4 2.3.6 3.6.6.6 0 1 .4 1 1V20c0 .6-.4 1-1 1A17 17 0 013 4c0-.6.4-1 1-1h3.5c.6 0 1 .4 1 1 0 1.3.2 2.5.6 3.6.1.3 0 .7-.2 1z"/></svg>
    Call Us
  </div>
  <svg class="abs" style="left:0;top:560px" width="1200" height="90" viewBox="0 560 1200 90">
    <path fill="#fff" d="M0 593 L470 593 Q600 640 730 593 L1200 593 L1200 650 L0 650Z"/>
    <path fill="#34a6d7" d="M0 584 L465 586 Q600 640 735 586 L1200 584 L1200 596 L745 598 Q600 656 455 598 L0 596Z"/>
    <rect x="589" y="572" width="22" height="34" rx="11" fill="none" stroke="#fff" stroke-width="2.5"/>
    <line x1="600" y1="580" x2="600" y2="588" stroke="#fff" stroke-width="2.5"/>
    <path d="M600 618v14M594 626l6 6 6-6" fill="none" stroke="#34a6d7" stroke-width="2.5"/>
  </svg>

  <div class="abs info-card" style="left:48px">
    <div class="ico"><svg width="26" height="32" viewBox="0 0 24 30"><path fill="#fff" d="M12 0a10 10 0 00-10 10c0 7.5 10 20 10 20s10-12.5 10-20A10 10 0 0012 0zm0 14a4 4 0 110-8 4 4 0 010 8z"/></svg></div>
    <div class="txt">Rue des Tilleuls<br>12, 4520 Velmot, Belgium</div>
  </div>
  <div class="abs info-card" style="left:426px">
    <div class="ico"><svg width="38" height="38" viewBox="0 0 40 40"><circle cx="20" cy="20" r="16" fill="none" stroke="#fff" stroke-width="3.5"/><path d="M20 10v11h8" fill="none" stroke="#fff" stroke-width="3.5" stroke-linecap="round"/></svg></div>
    <div class="txt center">Monday to Friday<br>7 am - 6 pm</div>
  </div>
  <div class="abs info-card" style="left:803px">
    <div class="ico"><svg width="34" height="34" viewBox="0 0 24 24"><path fill="#fff" d="M6.6 10.8a15.1 15.1 0 006.6 6.6l2.2-2.2c.3-.3.7-.4 1-.2 1.1.4 2.3.6 3.6.6.6 0 1 .4 1 1V20c0 .6-.4 1-1 1A17 17 0 013 4c0-.6.4-1 1-1h3.5c.6 0 1 .4 1 1 0 1.3.2 2.5.6 3.6.1.3 0 .7-.2 1z"/></svg></div>
    <div class="txt center" style="margin-left:58px">Call Us<br>+32 81 40 17 55</div>
  </div>

  <h2 class="abs section-title" style="left:0;top:856px;width:1200px;text-align:center">OUR SCHEDULES</h2>

  <div class="abs sched-card" style="left:48px">
    <div class="head">
      <svg class="ico" viewBox="0 0 94 94"><circle cx="47" cy="47" r="44" fill="#1a6fb0"/><circle cx="47" cy="47" r="37" fill="#fff"/><path d="M47 20v27l16 10" fill="none" stroke="#222" stroke-width="3" stroke-linecap="round"/><circle cx="47" cy="47" r="3" fill="#222"/></svg>
      <h3>OUR SCHEDULES AND DAYCARE</h3>
    </div>
    <ul class="sched-list">
      <li style="top:30px"><svg width="28" height="28" viewBox="0 0 28 28"><circle cx="14" cy="14" r="13" fill="#34a6d7"/><path d="M8 14h11M15 9l5 5-5 5" fill="none" stroke="#fff" stroke-width="2.5"/></svg>EVERY DAY FROM 8:25 AM TO 3:25 PM</li>
      <li style="top:83px"><svg width="28" height="28" viewBox="0 0 28 28"><circle cx="14" cy="14" r="13" fill="#34a6d7"/><path d="M8 14h11M15 9l5 5-5 5" fill="none" stroke="#fff" stroke-width="2.5"/></svg>WEDNESDAYS, FROM 8:25 AM TO 12:20 PM</li>
      <li style="top:136px"><svg width="28" height="28" viewBox="0 0 28 28"><circle cx="14" cy="14" r="13" fill="#34a6d7"/><path d="M8 14h11M15 9l5 5-5 5" fill="none" stroke="#fff" stroke-width="2.5"/></svg>A DAYCARE IS ORGANIZED FROM 7:00 AM</li>
      <li style="top:180px"><svg width="28" height="28" viewBox="0 0 28 28"><circle cx="14" cy="14" r="13" fill="#34a6d7"/><path d="M8 14h11M15 9l5 5-5 5" fill="none" stroke="#fff" stroke-width="2.5"/></svg>ON WEDNESDAYS, FROM 12:30 TO 18:00,<br>&nbsp;DIFFERENT ACTIVITIES ARE OFFERED</li>
    </ul>
  </div>

  <div class="abs sched-card" style="left:610px">
    <div class="head">
      <svg class="ico" viewBox="0 0 94 94"><circle cx="47" cy="47" r="44" fill="#cee9f5"/><circle cx="47" cy="47" r="36" fill="#fff" stroke="#85cae6" stroke-width="3"/><circle cx="47" cy="47" r="24" fill="#85cae6"/></svg>
      <h3>SCHOOL HOLIDAYS</h3>
    </div>
    <ul class="sched-list">
      <li style="top:30px"><svg width="28" height="28" viewBox="0 0 28 28"><circle cx="14" cy="14" r="13" fill="#34a6d7"/><path d="M8 14h11M15 9l5 5-5 5" fill="none" stroke="#fff" stroke-width="2.5"/></svg>BACK TO SCHOOL: MONDAY SEPTEMBER 3RD, 2019</li>
      <li style="top:83px"><svg width="28" height="28" viewBox="0 0 28 28"><circle cx="14" cy="14" r="13" fill="#34a6d7"/><path d="M8 14h11M15 9l5 5-5 5" fill="none" stroke="#fff" stroke-width="2.5"/></svg>FEAST OF THE FRENCH COMMUNITY: THU 27 SEPT 2019</li>
      <li style="top:136px"><svg width="28" height="28" viewBox="0 0 28 28"><circle cx="14" cy="14" r="13" fill="#34a6d7"/><path d="M8 14h11M15 9l5 5-5 5" fill="none" stroke="#fff" stroke-width="2.5"/></svg>WINTER HOLIDAYS (CHRISTMAS): DEC&nbsp; 24, 2019 TO&nbsp; JAN 4, 2020</li>
      <li style="top:189px"><svg width="28" height="28" viewBox="0 0 28 28"><circle cx="14" cy="14" r="13" fill="#34a6d7"/><path d="M8 14h11M15 9l5 5-5 5" fill="none" stroke="#fff" stroke-width="2.5"/></svg>SUMMER HOLIDAYS START ON MONDAY 1ST JULY 2020</li>
    </ul>
  </div>

  <p class="abs note">NOTE : ONLY THOSE CHILDREN WHOSE PARENTS HAVE PROVIDED A CERTIFICATE FROM THEIR EMPLOYER<br>SPECIFYING THE HOURS OF WORK WILL BE ACCEPTED&nbsp; AT THE DAY CARE CENTER.</p>

  <section class="abs news-bg"></section>
  <h2 class="abs section-title" style="left:50px;top:1535px">NEWS</h2>
  <div class="abs slider-arrows" style="left:1072px;top:1545px">
    <span><svg width="8" height="10" viewBox="0 0 8 10"><path d="M6 1L2 5l4 4" fill="none" stroke="#fff" stroke-width="1.8"/></svg></span>
    <span><svg width="8" height="10" viewBox="0 0 8 10"><path d="M2 1l4 4-4 4" fill="none" stroke="#fff" stroke-width="1.8"/></svg></span>
  </div>

  <article class="abs news-card" style="left:48px">
    <div class="photo" role="img" aria-label="Photo of a smiling boy in a blue shirt outdoors" style="background:linear-gradient(90deg,#8fc4d8 0%,#4f8fc4 25%,#6aa7d0 40%,#e7c4a6 55%,#f1d3b7 65%,#2f5aa8 80%,#6fa0c9 100%)"></div>
    <div class="badge">25<br>Sept</div>
    <h4>Loreum Ipsum Dummy Text</h4>
    <div class="meta"><span><svg width="14" height="14" viewBox="0 0 14 14"><circle cx="7" cy="4" r="3.5" fill="#777"/><path d="M0 14c0-4 3-6 7-6s7 2 7 6z" fill="#777"/></svg>Damien</span><span><svg width="20" height="14" viewBox="0 0 20 14"><ellipse cx="8" cy="6" rx="8" ry="5.5" fill="#777"/><path d="M3 9l-2 4 5-2z" fill="#777"/></svg>3 Comments</span></div>
    <p>Contrary to popular belief, Lorem Ipsum is not to simply random text. It has roots in a piece of&nbsp; the classi cal Latin literature.</p>
    <div class="more">» &nbsp;Read More</div>
  </article>

  <article class="abs news-card" style="left:423px">
    <div class="photo" role="img" aria-label="Photo of four smiling children with backpacks" style="background:linear-gradient(90deg,#f4e2d0 0%,#e4a373 15%,#d9463a 28%,#6e4530 42%,#e98a2e 55%,#f3c9a0 68%,#d94a3a 80%,#4d9fd6 92%,#e9dccd 100%)"></div>
    <div class="badge">2<br>Sept</div>
    <h4>Loreum Ipsum Dummy Text</h4>
    <div class="meta"><span><svg width="14" height="14" viewBox="0 0 14 14"><circle cx="7" cy="4" r="3.5" fill="#777"/><path d="M0 14c0-4 3-6 7-6s7 2 7 6z" fill="#777"/></svg>Lucas</span><span><svg width="20" height="14" viewBox="0 0 20 14"><ellipse cx="8" cy="6" rx="8" ry="5.5" fill="#777"/><path d="M3 9l-2 4 5-2z" fill="#777"/></svg>3 Comments</span></div>
    <p>Contrary to popular belief, Lorem Ipsum is not to simply random text. It has roots in a piece of&nbsp; the classi cal Latin literature.</p>
    <div class="more">» &nbsp;Read More</div>
  </article>

  <article class="abs news-card" style="left:800px">
    <div class="photo" role="img" aria-label="Photo of a girl reading a book in a classroom" style="background:linear-gradient(160deg,#e9e1d3 0%,#c8b9a4 25%,#d6cbb9 45%,#e7c4a6 60%,#f2c23c 78%,#e7e2d8 100%)"></div>
    <div class="badge">20<br>Sept</div>
    <h4>Loreum Ipsum Dummy Text</h4>
    <div class="meta"><span><svg width="14" height="14" viewBox="0 0 14 14"><circle cx="7" cy="4" r="3.5" fill="#777"/><path d="M0 14c0-4 3-6 7-6s7 2 7 6z" fill="#777"/></svg>Olivier</span><span><svg width="20" height="14" viewBox="0 0 20 14"><ellipse cx="8" cy="6" rx="8" ry="5.5" fill="#777"/><path d="M3 9l-2 4 5-2z" fill="#777"/></svg>3 Comments</span></div>
    <p>Contrary to popular belief, Lorem Ipsum is not to simply random text. It has roots in a piece of&nbsp; the classi cal Latin literature.</p>
    <div class="more">» &nbsp;Read More</div>
  </article>

  <section class="abs team-box">
    <h2 class="section-title" style="position:absolute;left:0;top:50px;width:738px;text-align:center">OUR TEACHING TEAM</h2>
    <div class="member" style="left:0"><div class="avatar" role="img" aria-label="Portrait of the teacher" style="background:radial-gradient(circle at 50% 45%,#e6b896 0,#d9a07c 30px,#efefef 46px,#e4e4e4 60px,#4a72a8 70px)"></div><h4>Sophie Marlier</h4><div class="section">Kindergarten section</div><div class="class">Holder of the class of M1</div></div>
    <div class="member" style="left:249px"><div class="avatar" role="img" aria-label="Portrait of the teacher" style="background:radial-gradient(circle at 50% 40%,#f0c9ac 0,#e2b293 26px,#5a3a2a 40px,#f2f2f2 52px,#222 66px)"></div><h4>Claire Deswaef</h4><div class="section">Primary section</div><div class="class">Holder of P1 class</div></div>
    <div class="member" style="left:510px"><div class="avatar" role="img" aria-label="Portrait of the teacher" style="background:radial-gradient(circle at 50% 45%,#d9a480 0,#c98e6a 30px,#3a2a22 44px,#ececec 56px,#5b6f8a 70px)"></div><h4>Mr Thibault</h4><div class="section">Primary section</div><div class="class">Holder of P6 class</div></div>
    <div class="dots"><span class="on"></span><span></span><span></span><span></span></div>
  </section>

  <aside class="abs contacts-box">
    <h2 class="section-title" style="position:absolute;left:0;top:50px;width:333px;text-align:center">USEFUL CONTACTS</h2>
    <div class="contacts-inner">
      <div class="contact-entry" style="top:22px">
        <h5>MRS HÉLÈNE FRAIPONT</h5>
        <div class="role">Prefect of studies</div>
        <div class="tel"><svg width="16" height="16" viewBox="0 0 24 24"><path fill="#34a6d7" d="M6.6 10.8a15.1 15.1 0 006.6 6.6l2.2-2.2c.3-.3.7-.4 1-.2 1.1.4 2.3.6 3.6.6.6 0 1 .4 1 1V20c0 .6-.4 1-1 1A17 17 0 013 4c0-.6.4-1 1-1h3.5c.6 0 1 .4 1 1 0 1.3.2 2.5.6 3.6.1.3 0 .7-.2 1z"/></svg>081 -00-0417</div>
      </div>
      <div class="contact-entry" style="top:146px">
        <h5>MRS JULIE VANDAMME</h5>
        <div class="role">Secretariat</div>
        <div class="tel"><svg width="16" height="16" viewBox="0 0 24 24"><path fill="#34a6d7" d="M6.6 10.8a15.1 15.1 0 006.6 6.6l2.2-2.2c.3-.3.7-.4 1-.2 1.1.4 2.3.6 3.6.6.6 0 1 .4 1 1V20c0 .6-.4 1-1 1A17 17 0 013 4c0-.6.4-1 1-1h3.5c.6 0 1 .4 1 1 0 1.3.2 2.5.6 3.6.1.3 0 .7-.2 1z"/></svg>081 -00-0417</div>
      </div>
      <div class="view-all">View All <svg width="16" height="14" viewBox="0 0 16 14"><path d="M1 7h13M8 1l6 6-6 6" fill="none" stroke="#fff" stroke-width="2.5"/></svg></div>
    </div>
  </aside>

  <h2 class="abs section-title" style="left:55px;top:2749px">ACTIVITIES</h2>
  <div class="abs slider-arrows" style="left:561px;top:2788px">
    <span><svg width="8" height="10" viewBox="0 0 8 10"><path d="M6 1L2 5l4 4" fill="none" stroke="#fff" stroke-width="1.8"/></svg></span>
    <span><svg width="8" height="10" viewBox="0 0 8 10"><path d="M2 1l4 4-4 4" fill="none" stroke="#fff" stroke-width="1.8"/></svg></span>
  </div>
  <article class="abs activity-card">
    <div class="photo" role="img" aria-label="Photo of the school sports hall interior"></div>
    <div class="date">SEPT<br>20</div>
    <h4>Loreum ipsum dummy text</h4>
    <div class="row" style="top:80px"><svg width="24" height="24" viewBox="0 0 24 24"><circle cx="12" cy="12" r="10" fill="none" stroke="#34a6d7" stroke-width="2"/><path d="M12 6v6h5" fill="none" stroke="#34a6d7" stroke-width="2"/></svg>12:00 p.m - 5:00 p.m</div>
    <div class="row" style="top:124px"><svg width="20" height="26" viewBox="0 0 24 30"><path fill="#34a6d7" d="M12 0a10 10 0 00-10 10c0 7.5 10 20 10 20s10-12.5 10-20A10 10 0 0012 0zm0 14a4 4 0 110-8 4 4 0 010 8z"/></svg>Loreum ipsum dummy text ,14th Etd.</div>
  </article>
  <div class="abs v-sep"></div>

  <aside class="abs rules-box">
    <span class="deco" style="left:10px;top:200px;width:60px;height:60px"></span>
    <span class="deco" style="left:65px;top:225px;width:40px;height:40px"></span>
    <span class="deco" style="left:380px;top:-10px;width:60px;height:60px"></span>
    <h3>RULES OF PROCEDURE</h3>
    <p>Please find attached the rules<br>of procedure:</p>
    <div class="rules-btn">
      <svg width="26" height="22" viewBox="0 0 26 22"><rect x="1" y="3" width="19" height="17" rx="2" fill="none" stroke="#fff" stroke-width="2"/><path d="M10 13L24 1M18 1h6v6" fill="none" stroke="#fff" stroke-width="2"/></svg>
      <span>Click Here to find<br>Attachmet</span>
    </div>
  </aside>

  <section class="abs gallery-bg"></section>
  <h2 class="abs section-title" style="left:48px;top:3138px">GALLERY</h2>
  <div class="abs slider-arrows" style="left:1076px;top:3148px">
    <span><svg width="8" height="10" viewBox="0 0 8 10"><path d="M6 1L2 5l4 4" fill="none" stroke="#fff" stroke-width="1.8"/></svg></span>
    <span><svg width="8" height="10" viewBox="0 0 8 10"><path d="M2 1l4 4-4 4" fill="none" stroke="#fff" stroke-width="1.8"/></svg></span>
  </div>
  <div class="abs g-img" role="img" aria-label="Photo of a girl in a green shirt reading in a kindergarten classroom" style="left:48px;top:3219px;width:344px;height:358px;background:linear-gradient(180deg,#d6c7b2 0%,#c2ae94 25%,#e6bfa0 42%,#9ed06a 62%,#86bd55 75%,#e9e2d4 88%,#7a6a5a 100%)"></div>
  <div class="abs g-img" role="img" aria-label="Photo of a teacher in front of a class" style="left:431px;top:3219px;width:335px;height:174px;background:linear-gradient(180deg,#e3d6c4 0%,#c9b59c 30%,#f0ece6 50%,#8a6a58 70%,#5a6f9c 100%)"></div>
  <div class="abs g-img" role="img" aria-label="Photo of children drawing together at a table" style="left:431px;top:3407px;width:335px;height:170px;background:linear-gradient(90deg,#b57a56 0%,#e7c6a4 22%,#d98b4a 40%,#f2d9b8 58%,#c96a5a 75%,#e8b98c 100%)"></div>
  <div class="abs g-img" role="img" aria-label="Photo of a toddler building with colourful blocks" style="left:801px;top:3219px;width:346px;height:358px;background:linear-gradient(160deg,#ffffff 0%,#f7f7f7 35%,#e7c7a9 48%,#d24a46 58%,#3a5aa8 70%,#f2f2f2 85%,#ffffff 100%)"></div>

  <div class="abs map" role="img" aria-label="Map of Belgium and surrounding region with the school location marked"></div>
  <section class="abs contact-panel">
    <h3>CONTACT US</h3>
    <div class="field" style="left:53px;top:133px;width:199px;height:41px">Name</div>
    <div class="field" style="left:292px;top:133px;width:199px;height:41px">Email</div>
    <div class="field" style="left:53px;top:205px;width:433px;height:77px">Message</div>
    <div class="submit"><svg width="20" height="18" viewBox="0 0 24 24"><path fill="#fff" d="M2 11l20-9-7 20-3-8z"/></svg>Submit</div>
  </section>

  <svg class="abs footer-deco" viewBox="0 4110 1200 140" width="1200" height="140">
    <circle cx="150" cy="4190" r="34" fill="#cee9f5" opacity=".6"/>
    <circle cx="860" cy="4180" r="38" fill="#cee9f5" opacity=".6"/>
    <circle cx="1110" cy="4195" r="32" fill="#cee9f5" opacity=".6"/>
    <path fill="#34a6d7" d="M0 4227 L460 4227 L545 4175 L655 4175 L740 4227 L1200 4227 L1200 4237 L0 4237Z"/>
    <path fill="#3e3e3e" d="M0 4233 L463 4233 L548 4181 L652 4181 L737 4233 L1200 4233 L1200 4250 L0 4250Z"/>
    <path d="M600 4192v-16M594 4182l6-6 6 6" fill="none" stroke="#fff" stroke-width="2.5"/>
    <rect x="591" y="4200" width="18" height="30" rx="9" fill="none" stroke="#fff" stroke-width="2.5"/>
    <line x1="600" y1="4208" x2="600" y2="4215" stroke="#fff" stroke-width="2.5"/>
  </svg>
  <footer class="abs footer">
    <div class="social"><span></span><span></span><span></span><span></span></div>
    <div class="copyright">© 2019 Copyrights&nbsp; @ Athenee Royal de Velmot All Rights Reserved</div>
  </footer>

</div>
</body>
</html>
```